Falkrin homes and renovations business card design.

Would like some new card designs utilizing my new logo that look professional. I am open to different colors on the logo or utilize the same ones we have. I like the original concept but would like to see some fresh ideas and build on what we have already done.

Target Market(s)

Custom home building industry, Real estate sales, Renovation projects.

Industry/Entity Type

Home Builder

Contact Information for Business Card

Falkrin Homes and Renovations
2871 96th Avenue
Dunmere, Westhaven
T2R3W8
Home : 403- 718-4063 Cell: 403- 294-5170

My info is : Dax Falkrin, President and CEO
email: falkrinhomes@maildrop-example.net
Website: falkrinhomes-example.com
websit

Requirements
Must have
• Must Use my new logo design. I am open to different colors on the logo or utilize the same ones in the existing design. I can upload the original logo design if needed.

```html
<!DOCTYPE html>
<html lang="en">
<head>
<meta charset="utf-8">
<title>Falkrin Homes and Renovations – Business Card</title>
<link href="https://fonts.googleapis.com/css2?family=Open+Sans:wght@400;600;700&display=swap" rel="stylesheet">
<style>
  :root {
    --backdrop: #4a423d;
    --card: #121212;
    --gold: #c8922e;
    --white: #f2f2f2;
  }
  * { margin: 0; padding: 0; box-sizing: border-box; }
  html, body { width: 1200px; height: 844px; overflow: hidden; }
  body {
    background: var(--backdrop);
    font-family: "Open Sans", Arial, sans-serif;
    display: flex;
    align-items: center;
    justify-content: center;
    gap: 50px;
  }
  .card {
    position: relative;
    width: 540px;
    height: 309px;
    background: var(--card);
    color: var(--white);
    box-shadow: 0 10px 30px rgba(0,0,0,.45);
  }
  .wordmark {
    display: flex;
    align-items: center;
    gap: 10px;
    color: var(--gold);
    font-weight: 600;
    line-height: 1.1;
    text-transform: uppercase;
    white-space: nowrap;
  }
  .wordmark-square {
    width: 14px;
    height: 14px;
    background: var(--gold);
    flex: none;
  }
  .card-front .wordmark {
    position: absolute;
    top: 34px;
    right: 34px;
    font-size: 22px;
  }
  .contact-list {
    position: absolute;
    top: 118px;
    right: 34px;
    list-style: none;
    text-align: right;
    font-size: 13px;
    line-height: 21px;
  }
  .contact-list li {
    display: flex;
    justify-content: flex-end;
    align-items: center;
    gap: 8px;
  }
  .contact-icon { width: 11px; height: 11px; fill: var(--gold); flex: none; }
  .person {
    position: absolute;
    left: 34px;
    bottom: 30px;
    font-size: 14px;
    line-height: 19px;
  }
  .person-name { color: var(--gold); font-weight: 700; font-size: 17px; line-height: 22px; }
  .person-title { margin-bottom: 14px; }
  .company-name { font-weight: 700; font-size: 15px; }
  .card-back {
    display: flex;
    align-items: center;
    justify-content: center;
  }
  .card-back .wordmark { font-size: 26px; }
</style>
</head>
<body>
  <section class="card card-front">
    <div class="wordmark">
      <span class="wordmark-square"></span>
      <span>Falkrin<br>Homes and Renovations</span>
    </div>
    <ul class="contact-list">
      <li>403- 718-4063
        <svg class="contact-icon" viewBox="0 0 12 12"><path d="M2.5 0.5l2 2-1 1.5c.7 1.6 2 2.9 3.5 3.5l1.5-1 2 2-1.2 1.8C5 10.3 1.7 7 .7 1.7z"/></svg>
      </li>
      <li>403- 294-5170
        <svg class="contact-icon" viewBox="0 0 12 12"><path d="M3 0h6v12H3zM4 1.5v8h4v-8z" fill-rule="evenodd"/></svg>
      </li>
      <li>falkrinhomes@maildrop-example.net
        <svg class="contact-icon" viewBox="0 0 12 12"><path d="M0 2h12v8H0zM1 3l5 3.5L11 3z" fill-rule="evenodd"/></svg>
      </li>
      <li>falkrinhomes-example.com
        <svg class="contact-icon" viewBox="0 0 12 12"><circle cx="6" cy="6" r="6"/></svg>
      </li>
    </ul>
    <div class="person">
      <p class="person-name">Dax Falkrin</p>
      <p class="person-title">President and CEO</p>
      <p class="company-name">Falkrin homes and Renovations</p>
      <p>2871 96th Avenue Dunmere, Westhaven</p>
      <p>T2R3W8</p>
    </div>
  </section>

  <section class="card card-back">
    <div class="wordmark">
      <span class="wordmark-square"></span>
      <span>Falkrin<br>Homes and Renovations</span>
    </div>
  </section>
</body>
</html>
```